Construction company that specializes in roofing and siding

https://maplecrestbuild.example/featured-projects/

https://www.bramwickhomesllc.example/#

https://www.tallgrovecontractors.example/residential-siding-services/

Please model a website after these examples
I posted a doc that has some content to get you started. I will upload more content and photos as the site progresses.

Coded - Design and coding required

5+ page

```html
<!DOCTYPE html>
<html lang="en">
<head>
<meta charset="utf-8">
<title>Stonebridge Construction</title>
<link href="https://fonts.googleapis.com/css2?family=Audiowide&family=Lato:wght@400;700&display=swap" rel="stylesheet">
<style>
:root{
  --orange:#d9560b;
  --orange-soft:#e8631a;
  --dark:#242424;
  --darker:#1e1e1e;
  --ink:#1a1a1a;
  --text:#333;
  --white:#fff;
  --grey:#f2f2f2;
}
*{box-sizing:border-box;margin:0;padding:0}
html,body{width:1200px;height:4194px;overflow:hidden}
body{position:relative;font-family:"Lato",sans-serif;color:var(--text);background:var(--white)}
.display{font-family:"Audiowide",sans-serif;text-transform:uppercase;letter-spacing:1px}
.abs{position:absolute}
.btn{position:absolute;display:flex;align-items:center;justify-content:center;background:var(--orange);color:var(--white);font-family:"Audiowide",sans-serif;text-transform:uppercase;font-size:16px;letter-spacing:1px;border-radius:3px}
.photo{position:absolute}

/* header */
.site-header{position:absolute;left:0;top:0;width:1200px;height:103px;background:var(--darker);z-index:5}
.brand-plate{position:absolute;left:0;top:0;height:103px;width:320px;background:var(--white);clip-path:polygon(0 0,100% 0,86% 100%,0 100%)}
.brand{position:absolute;left:110px;top:24px;display:flex;align-items:center;gap:12px}
.brand-mark{width:54px;height:54px;border-radius:50%;background:#555}
.brand-name{font-family:"Audiowide",sans-serif;font-size:20px;color:#555;text-transform:uppercase;line-height:1}
.main-nav{position:absolute;left:430px;top:26px;display:flex;gap:6px;font-size:14px;color:var(--white)}
.main-nav span{padding:8px 12px;border-radius:20px;display:flex;align-items:center;gap:5px}
.main-nav .active{background:#3a2a20;color:var(--orange-soft)}
.caret{width:0;height:0;border-left:4px solid transparent;border-right:4px solid transparent;border-top:5px solid #fff}

/* hero */
.hero-photo{left:0;top:85px;width:1200px;height:640px;background:linear-gradient(90deg,#2d3236 0%,#3d4a52 40%,#6c8590 70%,#5a6e5c 100%)}
.hero-title{left:111px;top:240px;font-size:54px;line-height:60px;color:var(--white)}
.hero-sub{left:111px;top:368px;width:560px;font-size:22px;line-height:30px;color:var(--orange-soft)}

/* about */
.about-photo{left:420px;top:640px;width:780px;height:520px;background:linear-gradient(90deg,#fff 0%,#d9dcdf 25%,#7e858c 55%,#4c5560 100%)}
.about-title{left:111px;top:828px;font-size:40px;color:var(--ink)}
.about-sub{left:111px;top:885px;font-size:20px;color:var(--orange)}
.about-copy{left:110px;top:927px;width:490px;font-size:14.5px;line-height:30px;color:#333}

/* services */
.section-title{width:1200px;left:0;text-align:center;font-size:36px;color:var(--ink)}
.frame{position:absolute;border-top:2px solid var(--orange);border-right:2px solid var(--orange)}
.service-card{position:absolute;width:458px;height:426px}
.service-label{position:absolute;right:8px;bottom:8px;background:var(--darker);color:var(--white);font-family:"Audiowide",sans-serif;font-size:19px;padding:7px 16px;text-transform:uppercase}
.siding-card{background:var(--orange);color:var(--white);text-align:center;padding:50px 32px 0}
.siding-card h3{font-family:"Audiowide",sans-serif;font-size:26px;font-weight:400}
.siding-card h4{font-family:"Audiowide",sans-serif;font-size:14px;font-weight:400;margin-top:6px}
.siding-card p{font-size:12.5px;line-height:24px;margin-top:18px}
.siding-card .btn-dark{display:inline-flex;margin-top:14px;background:var(--darker);color:#fff;font-family:"Audiowide",sans-serif;font-size:15px;padding:14px 30px;border-radius:3px}

/* promise */
.promise{left:0;top:2453px;width:1200px;height:653px;background:linear-gradient(135deg,#2c2c2c,#1f1f1f)}
.promise-ring{left:113px;top:2517px;width:520px;height:520px;border-radius:50%;border:20px solid var(--orange)}
.promise-photo{left:133px;top:2537px;width:480px;height:480px;border-radius:50%;background:linear-gradient(180deg,#8d97a4 0%,#c9c3b7 50%,#4c5a37 100%)}
.promise-title{left:669px;top:2578px;font-size:33px;line-height:44px;color:var(--white)}
.promise-copy{left:669px;top:2684px;width:410px;font-size:14.5px;line-height:30px;color:#e0e0e0}
.promise-sign{left:671px;top:2832px;font-size:15px;line-height:24px;color:var(--white)}

/* testimonials */
.t-card{position:absolute;top:3280px;width:315px;height:331px;padding:22px 20px}
.t-card.featured{background:#fff;box-shadow:0 4px 22px rgba(0,0,0,.12);border-radius:6px}
.t-head{display:flex;gap:14px;align-items:flex-start}
.avatar{width:70px;height:70px;border-radius:50%;background:#d8cfc6;flex:none}
.t-name{font-family:"Audiowide",sans-serif;font-size:16px;color:var(--ink);margin-top:8px;text-transform:uppercase}
.t-role{font-size:14px;color:#444;margin-top:4px}
.t-rule{width:48px;height:2px;background:var(--orange);margin-top:8px}
.stars{margin:14px 0 0 64px;display:flex;gap:4px}
.t-text{font-size:14.5px;line-height:26px;color:#333;margin-top:12px;padding-left:8px}
.arrow{position:absolute;top:3428px;width:22px;height:22px;border-radius:50%;display:flex;align-items:center;justify-content:center}

/* footer */
.footer{left:0;top:3700px;width:1200px;height:494px}
.footer-brand{left:110px;top:3835px;display:flex;align-items:center;gap:16px}
.footer-brand .brand-mark{width:74px;height:74px;background:#fff}
.footer-brand .brand-name{color:#fff;font-size:26px}
.socials{left:217px;top:3950px;display:flex;gap:8px}
.socials span{width:30px;height:30px;border-radius:50%;background:var(--orange)}
.socials span+span{background:#fff}
.footer-h{font-family:"Audiowide",sans-serif;font-size:16px;color:#fff;text-transform:uppercase;letter-spacing:1px}
.footer-p{font-size:14px;line-height:22px;color:#e0e0e0}
.subscribe{left:467px;top:3962px;width:256px;height:38px;border:1px solid #bbb;border-radius:20px;padding:0 6px 0 18px;display:flex;align-items:center;justify-content:space-between;font-size:13px;color:#ccc}
.subscribe i{width:28px;height:28px;border-radius:50%;background:var(--orange);display:block}
.contact-list{left:871px;top:3896px;list-style:none}
.contact-list li{display:flex;gap:14px;font-size:14px;line-height:22px;color:#e0e0e0;margin-bottom:10px}
.contact-list svg{flex:none;margin-top:4px}
.copyright{left:0;top:4138px;width:1200px;text-align:center;font-size:15px;color:#e0e0e0}
</style>
</head>
<body>

<header class="site-header">
  <div class="brand-plate"></div>
  <div class="brand"><span class="brand-mark"></span><span class="brand-name">Stonebridge<br><small style="font-size:10px">Construction</small></span></div>
  <nav class="main-nav">
    <span class="active">Home</span>
    <span>Roofing <i class="caret"></i></span>
    <span>Siding <i class="caret"></i></span>
    <span>Gutters</span>
    <span>Windows</span>
    <span>Repair <i class="caret"></i></span>
    <span>Storm damage repair <i class="caret"></i></span>
  </nav>
</header>

<section class="hero">
  <div class="photo hero-photo" role="img" aria-label="Blue-grey sided house with new shingle roof at dusk, darkened on the left"></div>
  <h1 class="abs display hero-title">Stonebridge<br>Construction</h1>
  <p class="abs display hero-sub">Stonebridge Construction is your source for roofing and siding in Minnesota.</p>
  <span class="btn" style="left:111px;top:477px;width:187px;height:52px">Get Started</span>
</section>

<section class="about">
  <svg class="abs" style="left:0;top:630px" width="1200" height="110" viewBox="0 0 1200 110">
    <path d="M0 88 L540 88 C590 88 610 18 670 18 L1200 18 L1200 110 L0 110Z" fill="#fff"/>
    <path d="M0 88 L540 88 C590 88 610 18 670 18 L1200 18 L1200 8 L660 8 C595 8 585 78 535 78 L0 78Z" fill="var(--orange)"/>
  </svg>
  <div class="photo about-photo" role="img" aria-label="Two roofers in hard hats nailing shingles on a roof" style="top:660px;clip-path:polygon(250px 0,100% 0,100% 100%,0 100%,0 58px,120px 58px)"></div>
  <h2 class="abs display about-title">About Us</h2>
  <p class="abs display about-sub">From humble beginnings</p>
  <p class="abs about-copy">In 2016 Dale Hartley started helping people with their home improvement projects. HIs very first job was installing window trim for a wonderful homeowner in Pine Hollow MN. He did his best work and made sure he treated his first customer like family. Afterall, his first customer was Rita Hartley, his Mom.</p>
  <span class="btn" style="left:111px;top:1092px;width:205px;height:49px">Learn More</span>
</section>

<section class="services">
  <h2 class="abs display section-title" style="top:1230px">Our Services</h2>

  <div class="frame" style="left:127px;top:1326px;width:460px;height:414px"></div>
  <div class="frame" style="left:629px;top:1326px;width:456px;height:414px"></div>
  <div class="frame" style="left:127px;top:1813px;width:460px;height:414px"></div>
  <div class="frame" style="left:629px;top:1813px;width:456px;height:414px"></div>

  <div class="service-card photo" style="left:112px;top:1340px;background:linear-gradient(180deg,#a9c7de 0%,#cfd6d8 40%,#3d434b 100%)" role="img" aria-label="Worker laying metal roofing panels on a house">
    <span class="service-label">Roofing</span>
  </div>
  <div class="service-card siding-card" style="left:615px;top:1340px">
    <h3>Siding</h3>
    <h4>Vinyl Siding</h4>
    <p>Vinyl siding is a great option to give your home’s exterior a beautiful makeover. A typical vinyl siding replacement can be completed in 3-5 days and costs about 15-25k. Vinyl siding is the most economical choice for siding replacement and with advances in paint technology it has become more resistant to fading than in the past. Stonebridge Construction specializes in vinyl siding replacement.</p>
    <span class="btn-dark">Learn More</span>
  </div>
  <div class="service-card photo" style="left:112px;top:1828px;background:linear-gradient(160deg,#c7d3dc 0%,#8a9aa6 45%,#2a5ab0 80%,#3c4048 100%)" role="img" aria-label="Worker in blue cap fitting a roof gutter">
    <span class="service-label">Gutters</span>
  </div>
  <div class="service-card photo" style="left:615px;top:1828px;background:linear-gradient(90deg,#5e6a60 0%,#b9c3c2 40%,#8c6a4e 75%,#4e4e50 100%)" role="img" aria-label="Installer fitting a large sliding glass window">
    <span class="service-label">Windows</span>
  </div>

  <span class="btn" style="left:506px;top:2305px;width:188px;height:49px">View More</span>
</section>

<section class="abs promise">
</section>
<div class="abs promise-ring"></div>
<div class="photo promise-photo" role="img" aria-label="Modern white farmhouse with dark roof and warm lit windows at dusk"></div>
<h2 class="abs display promise-title">The Stonebridge<br>Promise</h2>
<p class="abs promise-copy">You deserve timely service, high quality materials, expert installation, and a stonebridge warranty. That is what we promise to deliver. I invite you to put us to the test today. Sincerely</p>
<p class="abs display promise-sign">Dale Hartley, Owner<br>Stonebridge Construction</p>
<span class="btn" style="left:672px;top:2906px;width:168px;height:47px;font-size:14px">Learn More</span>

<section class="testimonials">
  <h2 class="abs display section-title" style="top:3178px">Testimonials</h2>

  <div class="arrow" style="left:68px;background:var(--orange)"><svg width="8" height="10" viewBox="0 0 8 10"><path d="M6 1 L2 5 L6 9" stroke="#fff" stroke-width="2" fill="none"/></svg></div>
  <div class="arrow" style="left:1146px;background:var(--ink)"><svg width="8" height="10" viewBox="0 0 8 10"><path d="M2 1 L6 5 L2 9" stroke="#fff" stroke-width="2" fill="none"/></svg></div>

  <div class="t-card" style="left:142px">
    <div class="t-head"><span class="avatar" role="img" aria-label="Customer portrait"></span><div><p class="t-name">Mara Ellison</p><p class="t-role">Lorem Ipsum</p><div class="t-rule"></div></div></div>
    <div class="stars">
      <svg width="100" height="16" viewBox="0 0 100 16"><g fill="#e9a21f"><path id="st" d="M8 1l2 5h5l-4 3 2 5-5-3-5 3 2-5-4-3h5z"/><use href="#st" x="20"/><use href="#st" x="40"/></g><g fill="none" stroke="#e9a21f"><use href="#st" x="60"/><use href="#st" x="80"/></g></svg>
    </div>
    <p class="t-text">Lorem ipsum dolor sit amet, consectetur adipiscing elit, sed do eiusmod tempor incididunt ut labore et dolore magna aliqua. Quis ipsum suspendisse ultrices gravida.</p>
  </div>

  <div class="t-card featured" style="left:472px">
    <div class="t-head"><span class="avatar" role="img" aria-label="Customer portrait"></span><div><p class="t-name">Nora Quill</p><p class="t-role">Lorem Ipsum</p><div class="t-rule"></div></div></div>
    <div class="stars"><svg width="100" height="16" viewBox="0 0 100 16"><g fill="#e9a21f"><use href="#st"/><use href="#st" x="20"/><use href="#st" x="40"/></g><g fill="none" stroke="#e9a21f"><use href="#st" x="60"/><use href="#st" x="80"/></g></svg></div>
    <p class="t-text">Lorem ipsum dolor sit amet, consectetur adipiscing elit, sed do eiusmod tempor incididunt ut labore et dolore magna aliqua. Quis ipsum suspendisse ultrices gravida. Risus commodo viverra maecenas</p>
  </div>

  <div class="t-card" style="left:802px">
    <div class="t-head"><span class="avatar" role="img" aria-label="Customer portrait"></span><div><p class="t-name">Theo Marsh</p><p class="t-role">Lorem Ipsum</p><div class="t-rule"></div></div></div>
    <div class="stars"><svg width="100" height="16" viewBox="0 0 100 16"><g fill="#e9a21f"><use href="#st"/><use href="#st" x="20"/><use href="#st" x="40"/></g><g fill="none" stroke="#e9a21f"><use href="#st" x="60"/><use href="#st" x="80"/></g></svg></div>
    <p class="t-text">Lorem ipsum dolor sit amet, consectetur adipiscing elit, sed do eiusmod tempor incididunt ut labore et dolore magna aliqua. Quis ipsum suspendisse ultrices gravida.</p>
  </div>
</section>

<footer class="abs footer">
  <svg class="abs" style="left:0;top:0" width="1200" height="494" viewBox="0 0 1200 494">
    <path d="M0 0 L540 0 C600 0 610 70 670 70 L1200 70 L1200 494 L0 494Z" fill="var(--darker)"/>
    <path d="M0 0 L540 0 C600 0 610 70 670 70 L1200 70 L1200 62 L675 62 C620 62 605 -8 545 -8 L0 -8Z" fill="var(--orange)"/>
    <path d="M0 0 L540 0 C600 0 610 70 670 70 L1200 70" stroke="var(--orange)" stroke-width="12" fill="none"/>
  </svg>
</footer>
<div class="abs footer-brand"><span class="brand-mark"></span><span class="brand-name">Stonebridge<br><small style="font-size:13px">Construction</small></span></div>
<div class="abs socials"><span></span><span></span><span></span></div>

<h3 class="abs footer-h" style="left:467px;top:3853px">Subscribe to our newsletter</h3>
<p class="abs footer-p" style="left:469px;top:3897px;width:270px">Lorem ipsum dolor sit amet, consectetur adipiscing elit, sed do</p>
<div class="abs subscribe"><span>Enter Your Email</span><i></i></div>

<h3 class="abs footer-h" style="left:871px;top:3853px">Contact Us</h3>
<ul class="abs contact-list">
  <li><svg width="12" height="14" viewBox="0 0 12 14"><path d="M6 0a5 5 0 0 0-5 5c0 4 5 9 5 9s5-5 5-9a5 5 0 0 0-5-5zm0 7a2 2 0 1 1 0-4 2 2 0 0 1 0 4z" fill="#fff"/></svg><span>48 Quarry Lane<br>Lorem ipsum dolor sit amet</span></li>
  <li><svg width="13" height="13" viewBox="0 0 13 13"><circle cx="6.5" cy="6.5" r="5.5" stroke="#fff" stroke-width="2" fill="none"/></svg><span>www.stonebridgebuild.example</span></li>
  <li><svg width="13" height="10" viewBox="0 0 13 10"><rect width="13" height="10" rx="1" fill="#fff"/><path d="M0 1l6.5 5L13 1" stroke="#1e1e1e" fill="none"/></svg><span>info@stonebridgebuild.example</span></li>
  <li><svg width="12" height="12" viewBox="0 0 12 12"><path d="M2 0h3l1 3-2 1a7 7 0 0 0 4 4l1-2 3 1v3a1 1 0 0 1-1 1A11 11 0 0 1 0 1a1 1 0 0 1 2-1z" fill="#fff"/></svg><span>555-010-0188</span></li>
</ul>

<p class="abs copyright">©Copyrights 2024 &nbsp; Stonebridge Construction &nbsp;| &nbsp; All Rights Reserved</p>

</body>
</html>
```